Detail Shop Business card design

i need a business card design for my new detailing company called 'Brisk's Polish Works'. i want an all black and white design . simple, direct and to the point. i want the designer to choose a fitting font to match the logothe front should have logo, address, phone and email and the back side should have a slogan and text indicating that we offer services on anything including cars, trucks, motorcycles and RVs. slogan will read "we take pride in your ride"
maybe also very small on the back side the IG icon with Brisks_Polish_Works

phone 208.417.6352
address 3847 E Larkin Ave
Spokane WA 99214
email: BrisksPolish@mailvexo.com

Target Market(s)

all ages , auto enthusiasts

Industry/Entity Type

Automotive

Contact Information for Business Card

the front should have logo, address, phone and email and the back side should have a slogan and text indicating that we offer services on anything including cars, trucks, motorcycles and RVs. slogan will read "we take pride in your ride"

phone 208.417.6352
address 3847 E Larkin Ave
Spokane WA 99214

Colors
000000
ffffff

Requirements
Must have
• bold font and very simple design with good spacing
Nice to have
• anything creative from the designer indicating we service any types of vehicles
Should not have
• any colors ,

```html
<!DOCTYPE html>
<html lang="en">
<head>
<meta charset="utf-8">
<title>Brisk's Polish Works – Business Card</title>
<link rel="stylesheet" href="https://fonts.googleapis.com/css2?family=Roboto+Slab:wght@400;700&display=swap">
<style>
  :root {
    --page: #1f1f21;
    --card: #111112;
    --card-edge: #2a2a2c;
    --ink: #ffffff;
    --ink-soft: #d8d8d8;
    --pattern-light: #1d1d1f;
    --pattern-dark: #121213;
  }
  * { margin: 0; padding: 0; box-sizing: border-box; }
  html, body { width: 1200px; height: 900px; overflow: hidden; }
  body {
    background: var(--page);
    font-family: "Roboto Slab", Georgia, serif;
    color: var(--ink);
    position: relative;
  }
  .card {
    position: absolute;
    left: 290px;
    width: 620px;
    height: 354px;
    background: var(--card);
    border: 1px solid var(--card-edge);
    border-radius: 4px;
    overflow: hidden;
  }
  .card--back { top: 70px; }
  .card--front { top: 470px; }

  /* Back */
  .back-pattern {
    position: absolute;
    inset: 0;
    background:
      radial-gradient(ellipse 70% 90% at 85% 35%, var(--pattern-light) 0%, transparent 75%),
      linear-gradient(100deg, var(--pattern-dark) 0%, #161617 55%, var(--pattern-light) 100%);
  }
  .back-mark {
    position: absolute;
    top: 122px; left: 0; width: 100%;
    text-align: center;
    font-size: 14px;
    font-weight: 700;
    letter-spacing: 0.04em;
    color: var(--ink);
  }
  .slogan {
    position: absolute;
    top: 240px; left: 0; width: 100%;
    display: flex; align-items: center; justify-content: center; gap: 12px;
    font-size: 15px; letter-spacing: 0.06em;
    color: var(--ink);
  }
  .slogan__rule { width: 44px; height: 1px; background: var(--ink-soft); }
  .services {
    position: absolute;
    top: 272px; left: 0; width: 100%;
    text-align: center;
    font-size: 15px; letter-spacing: 0.05em;
    color: var(--ink);
  }

  /* Front */
  .holder { position: absolute; top: 44px; left: 48px; }
  .holder__name { font-size: 24px; font-weight: 700; letter-spacing: 0.03em; }
  .holder__role { font-size: 13px; color: var(--ink-soft); margin-top: 2px; }
  .address {
    position: absolute; top: 138px; left: 48px;
    font-size: 16px; line-height: 1.45; font-style: normal;
  }
  .contacts {
    position: absolute; top: 238px; left: 48px;
    list-style: none;
    font-size: 16px; line-height: 1.5;
  }
  .contacts li { display: flex; align-items: center; gap: 9px; }
  .contacts svg { width: 12px; height: 12px; flex: none; }
  .brand {
    position: absolute; top: 150px; right: 40px;
    display: flex; align-items: center; gap: 12px;
    font-size: 22px; font-weight: 700; color: var(--ink);
  }
  .brand__dot {
    width: 14px; height: 14px; border-radius: 50%;
    border: 2px solid var(--ink-soft);
  }
</style>
</head>
<body>

<section class="card card--back" aria-label="Card back">
  <div class="back-pattern" role="img" aria-label="Faint repeated vehicle pattern across the card"></div>
  <div class="back-mark">Brisk's Polish Works</div>
  <p class="slogan"><span class="slogan__rule"></span>WE TAKE PRIDE IN YOUR RIDE<span class="slogan__rule"></span></p>
  <p class="services">CARS - TRUCKS - MOTORCYCLES AND RVS</p>
</section>

<section class="card card--front" aria-label="Card front">
  <div class="holder">
    <h1 class="holder__name">DARREN VALE</h1>
    <p class="holder__role">Director</p>
  </div>
  <address class="address">
    3847 E Larkin Ave<br>Spokane WA 99214
  </address>
  <ul class="contacts">
    <li>
      <svg viewBox="0 0 12 12" aria-hidden="true"><path d="M2.5 1 L4.5 1 L5 3.5 L3.8 4.5 Q5 7 7.5 8.2 L8.5 7 L11 7.5 L11 9.5 Q10.5 11 9 11 Q1 10 1 3 Q1 1.5 2.5 1 Z" fill="#fff"/></svg>
      208.417.6352
    </li>
    <li>
      <svg viewBox="0 0 12 12" aria-hidden="true"><rect x="1" y="2.5" width="10" height="7" fill="none" stroke="#fff" stroke-width="1.2"/><path d="M1 2.5 L6 6.5 L11 2.5" fill="none" stroke="#fff" stroke-width="1.2"/></svg>
      BrisksPolish@mailvexo.com
    </li>
    <li>
      <svg viewBox="0 0 12 12" aria-hidden="true"><circle cx="6" cy="6" r="5" fill="none" stroke="#fff" stroke-width="1"/><ellipse cx="6" cy="6" rx="2.2" ry="5" fill="none" stroke="#fff" stroke-width="1"/><path d="M1 6 H11" stroke="#fff" stroke-width="1"/></svg>
      www.BrisksPolish.com
    </li>
  </ul>
  <div class="brand">
    <span class="brand__dot" aria-hidden="true"></span>
    <span>Brisk's Polish Works</span>
  </div>
</section>

</body>
</html>
```